Meridale Bed Company Needs Business Card

Looking for a very nice looking business card. Creative but not extravagant. We sell beds and pillows across the U.S. and need something professional but catchy. I have attached the logo.

Name : Devin Holt
Title : President
Phone : (800) 471-2960
Email: sleep@quilmora.com
Website: www.quilmora.com

Can be single-sided or double-sided
horizontal or vertical

Can use Blues/Greys

Target Market(s)

Mass Market

Industry/Entity Type

Retail

Contact Information for Business Card

Name : Devin Holt
Title : President
Phone : (800) 471-2960
Email: sleep@quilmora.com
Website: www.quilmora.com

Requirements
Must have
• Clean, Modern, Smooth
• Can use Blues/Greys
• On the other side without the information - have something simple like www.quilmora.com or our logo
Nice to have
• Surprise me
Should not have
• Nothing crazy, nothing cluttered

```html
<!DOCTYPE html>
<html lang="en">
<head>
<meta charset="utf-8">
<title>Quilmora Business Card</title>
<link href="https://fonts.googleapis.com/css2?family=Quicksand:wght@400;500;700&display=swap" rel="stylesheet">
<style>
  :root {
    --sky: #36a3dc;
    --sky-soft: #52b5e0;
    --slate: #9d9d9d;
    --ink: #555555;
    --paper: #ffffff;
    --backdrop: #ececea;
  }
  * { margin: 0; padding: 0; box-sizing: border-box; }
  html, body { width: 1200px; height: 789px; overflow: hidden; }
  body {
    background: var(--backdrop);
    font-family: "Quicksand", sans-serif;
    position: relative;
  }
  .card {
    position: absolute;
    width: 540px;
    height: 309px;
    overflow: hidden;
    box-shadow: 0 6px 18px rgba(0,0,0,0.12);
  }
  .card svg.card-shapes { position: absolute; inset: 0; }
  .card-front { left: 40px; top: 240px; background: var(--paper); }
  .card-back { left: 620px; top: 240px; background: var(--slate); }

  .brand-name {
    position: absolute;
    font-family: "Quicksand", sans-serif;
    font-weight: 400;
    letter-spacing: 1px;
    line-height: 1;
    white-space: nowrap;
  }
  .card-front .brand-name {
    left: 24px; top: 42px;
    font-size: 56px;
    color: var(--sky);
  }
  .card-back .brand-name {
    left: 0; right: 0; top: 92px;
    text-align: center;
    font-size: 92px;
    color: var(--paper);
  }

  .person {
    position: absolute;
    right: 62px; top: 140px;
    text-align: right;
    white-space: nowrap;
  }
  .person-name { font-weight: 700; font-size: 19px; color: var(--sky); line-height: 1.1; }
  .person-title { font-weight: 500; font-size: 13px; color: var(--ink); margin-top: 2px; }
  .person-dot {
    position: absolute;
    right: 18px; top: 138px;
    width: 34px; height: 34px;
    border-radius: 50%;
    background: var(--slate);
  }

  .contact-list {
    position: absolute;
    left: 22px; top: 248px;
    list-style: none;
    color: var(--paper);
    font-size: 15px;
    font-weight: 500;
    white-space: nowrap;
  }
  .contact-list li { display: flex; align-items: center; gap: 8px; height: 24px; }
  .contact-icon { width: 17px; height: 17px; flex: none; }

  .web-line {
    position: absolute;
    display: flex; align-items: center; gap: 7px;
    color: var(--paper);
    font-weight: 500;
    white-space: nowrap;
  }
  .card-front .web-line { right: 16px; top: 270px; font-size: 13px; }
  .card-back .web-line { right: 22px; top: 262px; font-size: 18px; flex-direction: row-reverse; }
  .globe-icon { width: 15px; height: 15px; flex: none; }
  .card-back .globe-icon { width: 19px; height: 19px; }
</style>
</head>
<body>

  <section class="card card-front" aria-label="Card front">
    <svg class="card-shapes" width="540" height="309" viewBox="0 0 540 309">
      <line class="brand-rule" x1="292" y1="62" x2="524" y2="40" stroke="#36a3dc" stroke-width="1"/>
      <polygon class="footer-slate" points="0,212 320,212 370,309 0,309" fill="#9d9d9d"/>
      <polygon class="footer-sky" points="338,228 540,228 540,309 380,309" fill="#36a3dc"/>
    </svg>

    <div class="brand-name">quilmora</div>

    <div class="person">
      <div class="person-name">Devin Holt</div>
      <div class="person-title">President</div>
    </div>
    <div class="person-dot"></div>

    <ul class="contact-list">
      <li>
        <svg class="contact-icon" viewBox="0 0 17 17" aria-hidden="true">
          <rect width="17" height="17" rx="3" fill="#36a3dc"/>
          <path d="M5 3.5l2 2.2-1 1.3c.7 1.5 1.8 2.6 3.3 3.3l1.3-1 2.2 2-1.2 1.7C7.8 12.8 4.2 9.2 3.4 5z" fill="#fff"/>
        </svg>
        <span>(800) 471-2960</span>
      </li>
      <li>
        <svg class="contact-icon" viewBox="0 0 17 17" aria-hidden="true">
          <rect width="17" height="17" rx="3" fill="#36a3dc"/>
          <rect x="3.5" y="5" width="10" height="7.5" fill="#fff"/>
          <path d="M3.5 5l5 4 5-4" fill="none" stroke="#36a3dc" stroke-width="1"/>
        </svg>
        <span>sleep@quilmora.com</span>
      </li>
    </ul>

    <div class="web-line">
      <span>www.quilmora.com</span>
      <svg class="globe-icon" viewBox="0 0 16 16" aria-hidden="true">
        <rect width="16" height="16" rx="3" fill="#fff"/>
        <circle cx="8" cy="8" r="5" fill="none" stroke="#36a3dc" stroke-width="1"/>
        <ellipse cx="8" cy="8" rx="2.2" ry="5" fill="none" stroke="#36a3dc" stroke-width="1"/>
        <line x1="3" y1="8" x2="13" y2="8" stroke="#36a3dc" stroke-width="1"/>
      </svg>
    </div>
  </section>

  <section class="card card-back" aria-label="Card back">
    <svg class="card-shapes" width="540" height="309" viewBox="0 0 540 309">
      <polygon class="footer-sky-low" points="0,268 278,268 264,309 0,309" fill="#52b5e0"/>
      <polygon class="footer-sky-high" points="294,236 540,236 540,309 278,309" fill="#52b5e0"/>
    </svg>

    <div class="brand-name">quilmora</div>

    <div class="web-line">
      <span>www.quilmora.com</span>
      <svg class="globe-icon" viewBox="0 0 16 16" aria-hidden="true">
        <rect width="16" height="16" rx="3" fill="#fff"/>
        <circle cx="8" cy="8" r="5" fill="none" stroke="#52b5e0" stroke-width="1"/>
        <ellipse cx="8" cy="8" rx="2.2" ry="5" fill="none" stroke="#52b5e0" stroke-width="1"/>
        <line x1="3" y1="8" x2="13" y2="8" stroke="#52b5e0" stroke-width="1"/>
      </svg>
    </div>
  </section>

</body>
</html>
```